Harborline Renewal Business Card Design

Professional and clean design. The design colors should flow with the logo. Two-sided card with the website on the back which is:

www.HarborlineRenewal.example.

"Specializing in Water Damage Restoration"

On the front I need the name, email, phone, and logo.

Name: Darnell Quisby
Email: Darnell@HarborlineRenewal.example
Phone: 555-318-2046 for now

I only have the Preview and Thumbnail right now but should have the source files uploaded within a day or two.

Target Market(s)

Flood victims, home owners with water damage from busted pipes etc...

Industry/Entity Type

Business

Contact Information for Business Card

Name: Darnell Quisby

Font styles to use
Serif
Sans Serif

Requirements
Must have
• Business Card Details Info

```html
<!DOCTYPE html>
<html lang="en">
<head>
<meta charset="utf-8">
<title>Harborline Renewal — Business Card</title>
<link rel="stylesheet" href="https://fonts.googleapis.com/css2?family=Cinzel:wght@600&family=Crimson+Text:ital@0;1&display=swap">
<style>
  :root {
    --bg: #e9e7e4;
    --card-black: #1b1a1d;
    --card-white: #ffffff;
    --brand-blue: #2b9ad8;
    --text-light: #f4f4f4;
    --shadow: rgba(0, 0, 0, 0.18);
  }
  * { box-sizing: border-box; margin: 0; padding: 0; }
  html, body { width: 1200px; height: 676px; overflow: hidden; }
  body {
    background: var(--bg);
    display: flex;
    align-items: center;
    justify-content: center;
    gap: 56px;
  }
  .card {
    position: relative;
    width: 525px;
    height: 300px;
    overflow: hidden;
    box-shadow: 0 10px 28px var(--shadow);
    font-family: "Crimson Text", Georgia, serif;
  }

  /* Brand lockup */
  .brand {
    display: flex;
    align-items: center;
    gap: 12px;
  }
  .brand-name {
    font-family: "Cinzel", "Times New Roman", serif;
    font-weight: 600;
    color: var(--brand-blue);
    letter-spacing: 1px;
    line-height: 1;
    white-space: nowrap;
  }
  .brand-dot {
    border-radius: 50%;
    background: var(--brand-blue);
    flex: none;
  }

  /* Front */
  .card-front { background: var(--card-black); }
  .front-top {
    position: absolute;
    inset: 0 0 auto 0;
    height: 132px;
    background: var(--card-white);
    border-bottom: 7px solid var(--brand-blue);
    display: flex;
    flex-direction: column;
    align-items: flex-end;
    justify-content: center;
    padding-right: 34px;
    gap: 8px;
  }
  .front-top .brand-name { font-size: 27px; }
  .front-top .brand-dot { width: 40px; height: 40px; }
  .tagline {
    font-style: italic;
    font-size: 15px;
    color: var(--brand-blue);
    margin-right: 52px;
  }
  .contact {
    position: absolute;
    left: 34px;
    top: 156px;
    color: var(--text-light);
  }
  .contact-name {
    font-family: "Cinzel", "Times New Roman", serif;
    font-weight: 600;
    font-size: 19px;
    letter-spacing: 1.5px;
    margin-bottom: 10px;
  }
  .contact-list { list-style: none; }
  .contact-item {
    display: flex;
    align-items: center;
    gap: 9px;
    font-size: 15px;
    line-height: 23px;
  }
  .contact-icon { width: 13px; height: 13px; flex: none; }

  /* Back */
  .card-back {
    background: var(--card-black);
    display: flex;
    align-items: center;
    justify-content: center;
  }
  .card-back .brand-name { font-size: 30px; }
  .card-back .brand-dot { width: 44px; height: 44px; }
  .back-web {
    position: absolute;
    right: 30px;
    bottom: 30px;
    color: var(--text-light);
    font-style: italic;
    font-size: 15px;
  }
</style>
</head>
<body>

  <section class="card card-front" aria-label="Business card front">
    <header class="front-top">
      <div class="brand">
        <span class="brand-name">Harborline Renewal</span>
        <span class="brand-dot" aria-hidden="true"></span>
      </div>
      <p class="tagline">Specializing in Water Damage Restoration</p>
    </header>

    <div class="contact">
      <p class="contact-name">DARNELL QUISBY</p>
      <ul class="contact-list">
        <li class="contact-item">
          <svg class="contact-icon" viewBox="0 0 16 16" aria-hidden="true">
            <path fill="#2b9ad8" d="M3.6 1.2l2.3 2.6-1.2 1.8c.9 2 2.4 3.6 4.5 4.6l1.8-1.2 2.6 2.3-1.4 2.6C6.5 13.5 2.2 9.2 1.1 2.6z"/>
          </svg>
          <span>555-318-2046</span>
        </li>
        <li class="contact-item">
          <svg class="contact-icon" viewBox="0 0 16 16" aria-hidden="true">
            <rect x="1" y="3" width="14" height="10" fill="#2b9ad8"/>
            <path d="M1.5 3.5L8 9l6.5-5.5" fill="none" stroke="#1b1a1d" stroke-width="1.3"/>
          </svg>
          <span>Darnell@HarborlineRenewal.example</span>
        </li>
        <li class="contact-item">
          <svg class="contact-icon" viewBox="0 0 16 16" aria-hidden="true">
            <circle cx="8" cy="8" r="7" fill="#2b9ad8"/>
            <path d="M1 8h14M8 1c-3 3.5-3 10.5 0 14M8 1c3 3.5 3 10.5 0 14" fill="none" stroke="#1b1a1d" stroke-width="1"/>
          </svg>
          <span>www.HarborlineRenewal.example</span>
        </li>
      </ul>
    </div>
  </section>

  <section class="card card-back" aria-label="Business card back">
    <div class="brand">
      <span class="brand-name">Harborline Renewal</span>
      <span class="brand-dot" aria-hidden="true"></span>
    </div>
    <p class="back-web">www.HarborlineRenewal.example</p>
  </section>

</body>
</html>
```